Quintel Packaging Business Card

Project Overview
We are seeking a modern, minimalist business card that effectively represents our company while making a bold and lasting impression. The design should reflect trust, professionalism, and innovation, reinforcing our expertise in custom plastic manufacturing for warehouse and distribution centers.

Provided Assets & Specifications
Logo: We will provide our official logo for integration into the design.
Design Files: Photoshop (PSD) files for our printing specifications will be supplied.

Card Size & Material:
Dimensions: 3.5" x 2"
Material: 1/8" Radius Plastic Business Cards with 1/8" Rounded Corners
Clear plastic background—the design should strategically incorporate transparency.
Orientation: The card should be designed in landscape format for a sleek and professional presentation.

Design Requirements:
Logo Prominence
The logo must be the focal point of the card.
Space should be used effectively to draw attention to the logo while maintaining a minimalist layout.

Clear Plastic Integration
The transparent background should create the illusion of blank space, enhancing the modern and high-quality feel.
Avoid any frosted effects—we do not want white areas to appear semi-transparent.

Minimalist & Impactful
Clean, structured, and easy to read at a glance.
Focus on sharp contrast to ensure legibility and visibility.
The design should instill confidence and reflect our role as a leading plastics manufacturer.

Color Palette & Contrast
Primary Colors: Blue, Black, White, and Grey
Use bold black or blue for text and key elements to ensure they stand out against the clear plastic.
Avoid light, pastel, or neon colors that may fade into the plastic background.
No frosted or semi-transparent white—we do not want a cloudy effect.

Typography & Information Hierarchy
Bold, modern typography—clear, professional, and highly legible.
The business card should highlight:
Company Logo (Primary Focus)
Full Name & Title
Phone Number
Email
Website

Brand Representation
The card should reflect our expertise in manufacturing high-quality custom plastics for large-scale packaging and distribution businesses.
Our clients rely on us to enhance their brand presence through custom plastic solutions, and our business cards should reinforce that sense of precision and trust.

Final Considerations
Utilize the clear plastic effectively to differentiate our brand from standard business cards.
Maintain a sleek, professional aesthetic while ensuring all text and elements remain legible.
The design should align with our industry, conveying reliability and innovation.
We look forward to seeing a design that captures our brand identity, maximizes the clear plastic medium, and makes a strong, professional impact on our clients.

```html
<!DOCTYPE html>
<html lang="en">
<head>
<meta charset="utf-8">
<title>Quintel Packaging – Business Card</title>
<link rel="stylesheet" href="https://fonts.googleapis.com/css2?family=Lato:wght@400;700;900&display=swap">
<style>
  :root {
    --stage: #3a3a3b;
    --card-dark: #2f2f30;
    --card-dark-ink: #222223;
    --card-light: #ffffff;
    --ink: #1f1f20;
    --brand-blue: #0b86c1;
    --rule: #2a2a2a;
  }
  * { box-sizing: border-box; margin: 0; padding: 0; }
  html, body {
    width: 1200px; height: 689px; overflow: hidden;
    background: var(--stage);
    font-family: "Lato", Arial, sans-serif;
  }
  .stage { position: relative; width: 1200px; height: 689px; }

  .card {
    position: absolute; top: 196px;
    width: 520px; height: 297px;
    border-radius: 22px;
  }

  /* Back side */
  .card--back { left: 60px; background: var(--card-dark); }
  .card--back .wordmark {
    position: absolute; left: 50%; top: 50%;
    transform: translate(-50%, -50%);
    display: flex; align-items: center; gap: 18px;
    color: var(--card-dark-ink);
  }
  .card--back .wordmark__square { background: var(--card-dark-ink); }

  /* Front side */
  .card--front { left: 620px; background: var(--card-light); color: var(--ink); }

  .wordmark { display: flex; align-items: center; gap: 16px; }
  .wordmark__square { width: 54px; height: 54px; }
  .wordmark__name {
    font-weight: 900; font-size: 32px; line-height: 1.02;
    letter-spacing: 0.5px;
  }
  .card--front .wordmark {
    position: absolute; left: 44px; top: 42px; color: var(--brand-blue);
  }
  .card--front .wordmark__square { background: var(--ink); }

  .accent-tab {
    position: absolute; right: 0; top: 104px;
    width: 9px; height: 36px; background: var(--brand-blue);
  }

  .holder { position: absolute; right: 34px; top: 140px; text-align: right; }
  .holder__name { font-size: 21px; font-weight: 700; letter-spacing: 0.4px; text-transform: uppercase; }
  .holder__title { font-size: 13px; margin-top: 2px; }

  .divider {
    position: absolute; left: 34px; right: 24px; top: 203px;
    height: 1px; background: var(--rule);
  }

  .address {
    position: absolute; right: 34px; top: 220px;
    text-align: right; font-size: 13px; line-height: 1.45;
  }

  .contacts { position: absolute; left: 40px; top: 218px; list-style: none; font-size: 13px; }
  .contacts li { display: flex; align-items: center; gap: 9px; height: 21px; }
  .contacts svg { width: 13px; height: 13px; fill: var(--brand-blue); flex: none; }
</style>
</head>
<body>
<main class="stage">

  <section class="card card--back" aria-label="Card back">
    <div class="wordmark">
      <span class="wordmark__square"></span>
      <span class="wordmark__name">Quintel<br>Packaging</span>
    </div>
  </section>

  <section class="card card--front" aria-label="Card front">
    <div class="wordmark">
      <span class="wordmark__square"></span>
      <span class="wordmark__name">Quintel<br>Packaging</span>
    </div>

    <span class="accent-tab"></span>

    <div class="holder">
      <p class="holder__name">Marcus Hale</p>
      <p class="holder__title">Owner</p>
    </div>

    <span class="divider"></span>

    <address class="address" style="font-style:normal">
      88, Harbor Row Easton<br>30217, Northvale
    </address>

    <ul class="contacts">
      <li>
        <svg viewBox="0 0 24 24" aria-hidden="true"><path d="M6.6 10.8a15.1 15.1 0 0 0 6.6 6.6l2.2-2.2a1 1 0 0 1 1-.25 11.4 11.4 0 0 0 3.6.57 1 1 0 0 1 1 1V20a1 1 0 0 1-1 1A17 17 0 0 1 3 4a1 1 0 0 1 1-1h3.5a1 1 0 0 1 1 1c0 1.25.2 2.45.57 3.57a1 1 0 0 1-.25 1z"/></svg>
        <span>044-555 010 246</span>
      </li>
      <li>
        <svg viewBox="0 0 24 24" aria-hidden="true"><path d="M2 5h20v14H2z M2 5l10 8 10-8" /></svg>
        <span>info@quintelpack.com</span>
      </li>
      <li>
        <svg viewBox="0 0 24 24" aria-hidden="true"><circle cx="12" cy="12" r="10"/></svg>
        <span>www.quintelpack.com</span>
      </li>
    </ul>
  </section>

</main>
</body>
</html>
```